KBT Business Cards

We require business cards for our business. We would like a matte black back to the card, with our logo centred in the middle. The front side of the card is open to design.

Target Market(s)

Clients looking for legal services (professional)

Industry/Entity Type

Legal

Contact Information for Business Card

Doran Kelbrath
Partner
Mobile: 0461 738 524
Email: doran@kbtlaw.co
Website: www.kbtlaw.co
Level 3, 118 Wendmore Street
Sydney NSW 2000

Font styles to use
Other font styles liked:
• Avenir

Colors
f04a50
ffffff
1b1b1b

Requirements
Must have
• Black back with logo included in the centre of the card.
• Our font is Avenir.

```html
<!DOCTYPE html>
<html lang="en">
<head>
<meta charset="utf-8">
<title>KBT Business Cards</title>
<link href="https://fonts.googleapis.com/css2?family=Roboto:wght@400;700&display=swap" rel="stylesheet">
<style>
  :root {
    --backdrop: #5c5c5c;
    --card-dark: #231f20;
    --card-black: #1b1b1b;
    --brand-red: #c8203f;
    --red-top: #d2234b;
    --red-bottom: #a31c35;
    --text-light: #ffffff;
    --text-soft: #d9d9d9;
  }
  * { margin: 0; padding: 0; box-sizing: border-box; }
  html, body { width: 1200px; height: 802px; overflow: hidden; }
  body {
    background: var(--backdrop);
    font-family: "Roboto", sans-serif;
    position: relative;
  }
  .card {
    position: absolute;
    top: 274px;
    width: 443px;
    height: 264px;
    overflow: hidden;
    box-shadow: 0 3px 8px rgba(0,0,0,0.45);
  }
  .card-front { left: 136px; background: var(--card-dark); }
  .card-back {
    left: 624px;
    background: var(--card-black);
    display: flex;
    align-items: center;
    justify-content: center;
  }

  .red-field {
    position: absolute;
    inset: 0;
    width: 443px;
    height: 264px;
  }
  .contact {
    position: absolute;
    right: 37px;
    top: 84px;
    text-align: right;
    color: var(--text-light);
  }
  .contact-name {
    color: var(--brand-red);
    font-weight: 700;
    font-size: 15.5px;
    line-height: 18px;
  }
  .contact-role { font-size: 12.5px; line-height: 14px; margin-bottom: 9px; }
  .contact-line {
    font-size: 12.5px;
    line-height: 16px;
    display: flex;
    justify-content: flex-end;
    align-items: center;
    gap: 2px;
  }
  .contact-line svg { width: 9px; height: 9px; fill: var(--brand-red); }
  .contact-address {
    margin-top: 5px;
    font-size: 12.5px;
    line-height: 16px;
    color: var(--text-soft);
  }

  .brand {
    display: flex;
    align-items: center;
    gap: 14px;
  }
  .brand-square { width: 40px; height: 40px; background: var(--brand-red); }
  .brand-name {
    font-size: 52px;
    line-height: 56px;
    font-weight: 400;
    color: var(--text-light);
    letter-spacing: 1px;
  }
</style>
</head>
<body>

  <section class="card card-front">
    <svg class="red-field" viewBox="0 0 545 325" preserveAspectRatio="none" role="img" aria-label="Red diagonal panel where the brand pattern sits">
      <defs>
        <linearGradient id="redFade" x1="0" y1="0" x2="0" y2="1">
          <stop offset="0" stop-color="#d2234b"/>
          <stop offset="1" stop-color="#a31c35"/>
        </linearGradient>
      </defs>
      <polygon points="0,0 142,0 324,184 182,325 0,325" fill="url(#redFade)"/>
    </svg>

    <div class="contact">
      <p class="contact-name">DORAN KELBRATH</p>
      <p class="contact-role">Partner</p>
      <p class="contact-line">0461 738 524
        <svg viewBox="0 0 10 10"><path d="M1 4 Q5 0 9 4 L8 5 L6 4 L6 3 Q5 2.6 4 3 L4 4 L2 5 Z M2.5 5.5 H7.5 L8.5 9 H1.5 Z"/></svg>
      </p>
      <p class="contact-line">doran@kbtlaw.co
        <svg viewBox="0 0 10 10"><path d="M0.5 2 H9.5 V8 H0.5 Z"/><path d="M0.5 2 L5 5.5 L9.5 2" stroke="#231f20" stroke-width="0.9" fill="none"/></svg>
      </p>
      <p class="contact-line">www.kbtlaw.co
        <svg viewBox="0 0 10 10"><circle cx="5" cy="5" r="4.5"/><path d="M5 0.5 V9.5 M0.5 5 H9.5" stroke="#231f20" stroke-width="0.8"/></svg>
      </p>
      <p class="contact-address">Level 3, 118 Wendmore<br>Street, Sydney NSW 2000</p>
    </div>
  </section>

  <section class="card card-back">
    <div class="brand">
      <span class="brand-square"></span>
      <span class="brand-name">KBT</span>
    </div>
  </section>

</body>
</html>
```